A multi-page brochure that explains our firm ,KVL Wealth Management

We have a current brochure attached but it is a compilation of several items combined into one. We would like this to have the same content but be one complete theme. We are a financial planning form so it needs to have a level of professionalism but also a comfortable approach for clients and showing that was have a lot of resources and experience. We cater mostly to the 55-60+ age community.

We need the front page picture changed. lake themed would be great, like our website www.TheMoskaHouse.com
Just to be clear we use KVL Wealth Management now as our company name. Parent company name is The Moska House LLC. I attached the current mock brochure and our new logos.
Our logo colors are:
KVL WM Logo Colors:

Blue:
HEX: #0f75bc
RGB: rgba(15,117,188,255)

Grey:
HEX: #6d6e71
RGB: rgba(109,110,113,255)

Target Market(s)

High-level individuals that are looking for financial guidance who are 40 years old and up

Industry/Entity Type

Wealth Management

Requirements
Must have
• Clean and crisp
Nice to have
• https://www.bramblestoneplanners.com/wealth-management-brochure , this is a sample we like

```html
<!DOCTYPE html>
<html lang="en">
<head>
<meta charset="UTF-8">
<title>KVL Wealth Management Brochure</title>
<link href="https://fonts.googleapis.com/css2?family=Playfair+Display:wght@400;500&family=Poppins:wght@400;500;600&display=swap" rel="stylesheet">
<style>
  :root {
    --brand-blue: #0f75bc;
    --brand-grey: #6d6e71;
    --band-blue: #1566ae;
    --sky: #8fc4ee;
    --ink: #1f1f1f;
    --paper: #ffffff;
  }
  * { box-sizing: border-box; margin: 0; padding: 0; }
  html, body { width: 1004px; height: 1200px; overflow: hidden; }
  body {
    background: var(--sky);
    position: relative;
    font-family: 'Poppins', sans-serif;
    color: var(--ink);
  }
  .page {
    position: absolute;
    width: 428px;
    height: 553px;
    background: var(--paper);
    overflow: hidden;
  }
  .page--cover { left: 44px; top: 34px; }
  .page--partner { left: 501px; top: 34px; }
  .page--about { left: 44px; top: 609px; }
  .page--philosophy { left: 501px; top: 609px; }

  .abs { position: absolute; }
  .photo { position: absolute; }

  /* Cover */
  .cover-photo {
    inset: 0;
    background: linear-gradient(180deg, #4b5560 0%, #6d7178 28%, #8a6a48 48%, #3a3f46 62%, #1c2128 80%, #0f1317 100%);
  }
  .logo-box {
    position: absolute; left: 0; top: 24px;
    width: 235px; height: 62px;
    background: var(--paper);
    display: flex; align-items: center; justify-content: center;
  }
  .logo-name {
    font-family: 'Playfair Display', serif;
    font-weight: 400;
    font-size: 17px;
    color: var(--brand-blue);
    letter-spacing: 0.2px;
  }
  .cover-welcome {
    left: 17px; top: 349px;
    font-size: 11px; color: #fff;
  }
  .cover-title {
    left: 17px; top: 372px; width: 405px;
    font-family: 'Playfair Display', serif;
    font-size: 30px; line-height: 37px;
    color: #fff; font-weight: 400;
  }

  /* Shared */
  .page-title {
    position: absolute; left: 31px; top: 22px;
    font-family: 'Playfair Display', serif;
    font-size: 21px; font-weight: 400;
    color: var(--brand-grey);
  }
  .page-title .accent { color: var(--brand-blue); }
  .body-text {
    position: absolute;
    font-size: 9px; line-height: 14px;
    text-align: justify;
    color: var(--ink);
  }
  .body-text p + p { margin-top: 14px; }
  .footer {
    position: absolute; left: 0; bottom: 0;
    width: 100%; height: 30px;
    background: var(--brand-grey);
    color: #fff;
    font-size: 7.5px; font-weight: 500;
    display: flex; align-items: center; justify-content: space-between;
    padding: 0 30px 0 32px;
  }

  /* Partner page */
  .partner-band {
    left: 0; top: 0; width: 428px; height: 145px;
    background: linear-gradient(120deg, #1a6db8 0%, var(--band-blue) 55%, #125a9c 100%);
  }
  .partner-title {
    left: 31px; top: 60px;
    font-family: 'Playfair Display', serif;
    font-size: 20.5px; color: #fff;
  }
  .partner-portrait {
    left: 23px; top: 321px; width: 174px; height: 174px;
    border-radius: 50%;
    background: radial-gradient(circle at 40% 40%, #e8e6e2 0%, #b9b5ae 55%, #6d6862 100%);
  }
  .partner-arc { left: 100px; top: 316px; }
  .partner-aside {
    left: 232px; top: 338px; width: 168px;
    font-size: 8px; line-height: 14px;
  }
  .partner-aside p + p { margin-top: 14px; }

  /* About page */
  .about-photo {
    left: 28px; top: 122px; width: 174px; height: 239px;
    background: linear-gradient(160deg, #e7e1d8 0%, #c9a98a 50%, #8b6a52 100%);
  }
  .principles {
    position: absolute; left: 218px; top: 121px; width: 180px;
  }
  .principle + .principle { margin-top: 11px; }
  .principle-name {
    font-size: 8.5px; font-weight: 600; color: var(--brand-blue);
    letter-spacing: 0.2px; margin-bottom: 4px;
  }
  .principle-text { font-size: 9px; line-height: 14px; text-align: justify; }
  .footnote {
    position: absolute; left: 31px; top: 475px; width: 366px;
    font-size: 8px; line-height: 13px; color: var(--brand-blue);
  }

  /* Philosophy page */
  .team-photo {
    left: 221px; top: 129px; width: 183px; height: 148px;
    background: linear-gradient(180deg, #b9cbd6 0%, #8ea58a 40%, #5b6f8a 70%, #3d4f6a 100%);
  }
  .city-photo {
    left: 23px; top: 266px; width: 183px; height: 148px;
    background: linear-gradient(180deg, #06090d 0%, #0d1a22 55%, #1f3a44 80%, #3a4a40 100%);
  }
</style>
</head>
<body>

  <!-- Cover -->
  <section class="page page--cover">
    <div class="photo cover-photo" role="img" aria-label="Lakeside city skyline with autumn trees reflected in calm water"></div>
    <div class="logo-box"><span class="logo-name">KVL Wealth Management</span></div>
    <p class="abs cover-welcome">Welcome To KVL Wealth Management</p>
    <h1 class="abs cover-title">Wealth Management Focused on Your Needs and Vision</h1>
  </section>

  <!-- Page 1 -->
  <section class="page page--partner">
    <div class="photo partner-band" role="img" aria-label="Blue-tinted hand holding a phone showing market prices"></div>
    <h2 class="abs partner-title">Partner with a Specialist</h2>
    <div class="body-text" style="left:31px; top:165px; width:367px;">
      <p>Understanding your unique needs and vision for the future is the foundation of our relationship. Together, we evaluate your current financial position and define where you want to go.</p>
      <p>From there, we develop a comprehensive wealth management strategy designed to support both your immediate priorities and long-term aspirations.</p>
      <p>And because life is never entirely predictable, we also prepare for the unexpected helping you stay confident and secure through whatever changes may lie ahead.</p>
    </div>
    <div class="photo partner-portrait" role="img" aria-label="Advisor working on a laptop, circular portrait"></div>
    <svg class="abs partner-arc" width="110" height="140" viewBox="0 0 110 140" aria-hidden="true">
      <path d="M10 3 A92 92 0 0 1 80 134" fill="none" stroke="var(--brand-blue)" stroke-width="2.2" stroke-linecap="round"/>
    </svg>
    <div class="abs partner-aside">
      <p>Exploring the topics highlighted in this brochure will give you a clear sense of the depth and breadth of our services.</p>
      <p>Throughout the planning process, we partner closely with you continually returning to the question that matters most: what is truly right for you and your loved ones?</p>
    </div>
    <footer class="footer"><span>Copyright@2026.All Rights Reserved</span><span>Page 1</span></footer>
  </section>

  <!-- Page 2 -->
  <section class="page page--about">
    <h2 class="page-title"><span class="accent">About Our</span> Firm</h2>
    <div class="body-text" style="left:30px; top:60px; width:367px;">
      <p>The Moska House LLC, established in 1987, is an independent, full-service, financial consulting firm.As we search the marketplace for innovative, strategic solutions, The Moska House is guided by the following principles:</p>
    </div>
    <div class="photo about-photo" role="img" aria-label="Three women looking at a laptop together"></div>
    <div class="principles">
      <div class="principle">
        <h3 class="principle-name">SERVICE</h3>
        <p class="principle-text">We seek to anticipate your needs and exceed your expectations in every aspect of our partnership.</p>
      </div>
      <div class="principle">
        <h3 class="principle-name">PLANNING</h3>
        <p class="principle-text">We collaborate with you by listening, asking questions, educating and helping you make informed decisions to skillfully implement appropriate, effective financial strategies.</p>
      </div>
      <div class="principle">
        <h3 class="principle-name">INTEGRITY</h3>
        <p class="principle-text">We build long-term client relationships and are proud of the integrity and sensitivity we exhibit when working with all our clients.</p>
      </div>
    </div>
    <div class="body-text" style="left:31px; top:386px; width:366px;">
      <p>The Moska House has created an environment of objectivity and independence in which to provide independent guidance and access to the widest variety of fiscal tools to support your financial goals. Our work complements the services of your existing advisors, including CPAs and attorneys.* The degree and sophistication of the plan varies according to your circumstances.</p>
    </div>
    <p class="footnote">*The Moska House LLC does not provide specific tax or legal advice. Please consult your accountant and/or attorney regarding your specific situation.</p>
    <footer class="footer"><span>Copyright@2026.All Rights Reserved</span><span>Page 2</span></footer>
  </section>

  <!-- Page 3 -->
  <section class="page page--philosophy">
    <h2 class="page-title"><span class="accent">Our</span> Philosophy</h2>
    <div class="body-text" style="left:29px; top:60px; width:368px;">
      <p>Our philosophy is based on empowering our clients through education. After taking the time to understand your goals, needs and challenges, we help you to understand and organize all aspects of your finances and create a plan of action.</p>
    </div>
    <div class="body-text" style="left:27px; top:125px; width:172px;">
      <p>The framework used to develop your plan is the 6-step Wealth Management Process, a flexible system that allows us to effectively customize a plan suited to your unique circumstances. During each step of the process, we take the time to provide a detailed explanation of our recommendations and why they are best suited for your situation.</p>
    </div>
    <div class="photo team-photo" role="img" aria-label="Four advisors in suits standing on a balcony with city view"></div>
    <div class="photo city-photo" role="img" aria-label="City skyline lit up at night"></div>
    <div class="body-text" style="left:225px; top:296px; width:175px;">
      <p>After all your questions have been answered, and you are confident in your decisions, we begin to implement a course of action. By actively learning and participating in the planning process, you retain control each step of the way. Once your investment program is implemented, we will monitor the performance of your investments and consult with you regularly to help ensure that the program continues to reflect your goals and objectives.</p>
    </div>
    <div class="body-text" style="left:23px; top:431px; width:180px;">
      <p>The Moska House strives to develop a relationship in which you will feel more knowledgeable, informed and empowered as a result of working with us.</p>
    </div>
    <footer class="footer"><span>Copyright@2026.All Rights Reserved</span><span>Page 3</span></footer>
  </section>

</body>
</html>
```